RWT Fittings Ltd Business Cards

We need a business card with our business logo. We provide window and door installations on high-rises in west coast British Colombia, Canada.

I would like my business information and details on one side of the card, and the other side the company name with logo

Target Market(s)

General Contractors

Industry/Entity Type

Construction

Contact Information for Business Card

one side i want my company name and logo in the dark theme logo that i provided

Requirements
Must have
• Marco Peltieri, 16045518293, RWTFittings@mailbox-demo.com, 1407-5194 Linden Row Burnaby BC, V5H 2K9, Owner & Manager

```html
<!DOCTYPE html>
<html lang="en">
<head>
<meta charset="utf-8">
<title>RWT Fittings Ltd – Business Cards</title>
<link href="https://fonts.googleapis.com/css2?family=Poppins:wght@300;400;600;700&display=swap" rel="stylesheet">
<style>
  :root {
    --page-bg: #d6d6d6;
    --card-light: #ffffff;
    --card-dark: #242424;
    --brand-blue: #1f9fdb;
    --text-grey: #555555;
    --wordmark-dark: #c4c4c4;
  }
  * { margin: 0; padding: 0; box-sizing: border-box; }
  html, body {
    width: 1200px; height: 965px; overflow: hidden;
    background: var(--page-bg);
    font-family: "Poppins", sans-serif;
  }
  .card {
    position: absolute; top: 159px;
    width: 383px; height: 669px;
  }
  .card--front { left: 186px; background: var(--card-light); }
  .card--back  { left: 653px; background: var(--card-dark); }

  .wordmark {
    position: absolute; left: 0; right: 0; top: 62px;
    display: flex; align-items: center; justify-content: center; gap: 14px;
    font-weight: 600; color: var(--brand-blue);
  }
  .wordmark__mark { width: 46px; height: 46px; background: currentColor; }
  .wordmark__text { line-height: 1; }
  .wordmark__name { display: block; font-size: 58px; letter-spacing: 1px; }
  .wordmark__sub { display: block; font-size: 14px; letter-spacing: 3px; margin-top: 6px; }
  .card--back .wordmark { color: var(--wordmark-dark); top: 60px; }

  .person {
    position: absolute; left: 0; right: 0; top: 400px; text-align: center;
  }
  .person__name {
    font-size: 27px; font-weight: 700; color: var(--brand-blue);
    letter-spacing: 0.3px; line-height: 1.1;
  }
  .person__role {
    font-size: 15px; font-weight: 300; color: var(--text-grey); line-height: 1.3;
  }

  .contact-divider {
    position: absolute; top: 462px; left: 29px; right: 27px; height: 22px;
    display: flex; align-items: center; gap: 8px;
  }
  .contact-divider__line { flex: 1; height: 1.5px; background: var(--brand-blue); }
  .contact-divider__icons { display: flex; gap: 8px; padding: 0 8px; }
  .icon-dot {
    width: 21px; height: 21px; border-radius: 50%; background: var(--brand-blue);
    display: flex; align-items: center; justify-content: center;
  }
  .icon-dot svg { width: 12px; height: 12px; }

  .contact-list {
    position: absolute; left: 0; right: 0; top: 493px; text-align: center;
    font-size: 16px; font-weight: 300; color: var(--text-grey); line-height: 20px;
    list-style: none;
  }
  .address-rule {
    position: absolute; top: 570px; left: 30px; right: 30px;
    height: 1.5px; background: var(--brand-blue);
  }
  .address {
    position: absolute; left: 0; right: 0; top: 580px; text-align: center;
    font-size: 15.5px; font-weight: 300; color: var(--text-grey); font-style: normal;
  }
</style>
</head>
<body>

<section class="card card--front" aria-label="Business card front">
  <div class="wordmark">
    <span class="wordmark__mark"></span>
    <span class="wordmark__text">
      <span class="wordmark__name">RWT</span>
      <span class="wordmark__sub">FITTINGS LTD</span>
    </span>
  </div>

  <div class="person">
    <p class="person__name">MARCO PELTIERI</p>
    <p class="person__role">Owner &amp; Manager</p>
  </div>

  <div class="contact-divider">
    <span class="contact-divider__line"></span>
    <span class="contact-divider__icons">
      <span class="icon-dot" aria-label="Phone">
        <svg viewBox="0 0 24 24" fill="#fff"><path d="M6.6 10.8a15 15 0 0 0 6.6 6.6l2.2-2.2a1 1 0 0 1 1-.25 11.4 11.4 0 0 0 3.6.57 1 1 0 0 1 1 1V20a1 1 0 0 1-1 1A17 17 0 0 1 3 4a1 1 0 0 1 1-1h3.5a1 1 0 0 1 1 1c0 1.25.2 2.45.57 3.57a1 1 0 0 1-.25 1z"/></svg>
      </span>
      <span class="icon-dot" aria-label="Email">
        <svg viewBox="0 0 24 24" fill="none" stroke="#fff" stroke-width="2"><rect x="3" y="5" width="18" height="14" rx="1"/><path d="M3 6l9 7 9-7"/></svg>
      </span>
      <span class="icon-dot" aria-label="Website">
        <svg viewBox="0 0 24 24" fill="none" stroke="#fff" stroke-width="1.8"><circle cx="12" cy="12" r="9"/><ellipse cx="12" cy="12" rx="4" ry="9"/><path d="M3 12h18M5 7h14M5 17h14"/></svg>
      </span>
    </span>
    <span class="contact-divider__line"></span>
  </div>

  <ul class="contact-list">
    <li>604-551-8293</li>
    <li>RWTFittings@mailbox-demo.com</li>
    <li>www.rwtfittings-demo.com</li>
  </ul>

  <div class="address-rule"></div>
  <address class="address">1407-5194 Linden Row Burnaby BC, V5H 2K9</address>
</section>

<section class="card card--back" aria-label="Business card back">
  <div class="wordmark">
    <span class="wordmark__mark"></span>
    <span class="wordmark__text">
      <span class="wordmark__name">RWT</span>
      <span class="wordmark__sub">FITTINGS LTD</span>
    </span>
  </div>
</section>

</body>
</html>
```